BUSINESS CARD - HALLORAN FIELD SERVICES

I would like to create a business card for my fertilizer spreading business. I would like to incorporate my existing logo and also a description of the services offered. The business card will be given to farmers so must be kept simple but effective. It will also be left in stores so much also be eye catching in order to stand out from other cards.

Target Market(s)

FARMERS

Requirements
Must have
• FRONT OF CARD = EXISTING LOGO + "CUSTOMISED SPREADING" below the logo

REAR Of CARD = SERVICES OFFERED AND CONTACT DETAILS

- Bulk fertilizer including Lime, Gypsum, Manure & Compost
- Granular fertilizer including Single Super, Urea, Terragran, & Custom Blends
- Modern equipment - Autosteer & Variable Rate Capable
- Friendly & Reliable Service
- Contact Gus: 0417 552 308
Nice to have
• utilize same color scheme as existing logo

```html
<!DOCTYPE html>
<html lang="en">
<head>
<meta charset="utf-8">
<title>Halloran Field Services – Business Card</title>
<link href="https://fonts.googleapis.com/css2?family=Montserrat:wght@500;700&family=Oswald:wght@500;600&display=swap" rel="stylesheet">
<style>
  :root {
    --stage: #2b2b2b;
    --card-dark: #4a4a4c;
    --card-dark-edge: #3c3c3e;
    --band: #545456;
    --paper: #ffffff;
    --paper-shade: #dcdcdc;
    --ink: #555557;
    --ink-soft: #3f3f41;
    --orange: #f7941d;
    --rule: #a8a8a8;
  }
  * { margin: 0; padding: 0; box-sizing: border-box; }
  html, body { width: 1200px; height: 1015px; overflow: hidden; }
  body {
    background: var(--stage);
    font-family: "Montserrat", Arial, sans-serif;
    position: relative;
  }
  .card {
    position: absolute;
    left: 285px;
    width: 630px;
    height: 360px;
    border-radius: 4px;
    overflow: hidden;
    box-shadow: 0 10px 30px rgba(0,0,0,.55);
  }

  /* Front */
  .card--front {
    top: 75px;
    background: linear-gradient(160deg, var(--card-dark) 0%, var(--card-dark-edge) 100%);
  }
  .front__texture {
    position: absolute; inset: 0;
    background: radial-gradient(ellipse at 70% 20%, rgba(255,255,255,.08), rgba(0,0,0,0) 60%);
  }
  .front__brand {
    position: absolute;
    left: 0; right: 0; top: 118px;
    display: flex; align-items: center; justify-content: center; gap: 12px;
  }
  .front__dot {
    width: 28px; height: 28px; border-radius: 50%; background: var(--paper);
  }
  .front__name {
    font-weight: 700; font-size: 20px; letter-spacing: 1px;
    color: var(--paper);
  }
  .front__tagline {
    position: absolute; left: 0; right: 0; top: 182px;
    text-align: center;
    font-family: "Oswald", "Arial Narrow", sans-serif;
    font-weight: 600; font-size: 40px; letter-spacing: .5px;
    color: var(--orange);
  }

  /* Back */
  .card--back {
    top: 560px;
    background: linear-gradient(180deg, var(--paper) 0%, var(--paper) 45%, var(--paper-shade) 100%);
  }
  .back__brand {
    position: absolute; left: 30px; top: 95px; width: 255px;
    display: flex; flex-direction: column; align-items: center; gap: 12px;
  }
  .back__dot { width: 44px; height: 44px; border-radius: 50%; background: var(--ink); }
  .back__name {
    font-weight: 700; font-size: 21px; line-height: 1.2; text-align: center;
    color: var(--ink);
  }
  .back__divider {
    position: absolute; left: 300px; top: 40px; width: 1px; height: 190px;
    background: var(--rule);
  }
  .services {
    position: absolute; left: 318px; top: 38px; width: 300px;
    list-style: none;
    font-weight: 500; font-size: 14.5px; line-height: 1.3;
    color: var(--ink-soft);
  }
  .services li { position: relative; padding-left: 20px; margin-bottom: 5px; }
  .services li::before {
    content: ""; position: absolute; left: 0; top: 5px;
    width: 10px; height: 10px; border-radius: 50%; background: var(--orange);
  }
  .contact-band {
    position: absolute; left: 0; right: 0; bottom: 0; height: 92px;
    background: var(--band);
    display: flex; align-items: center; justify-content: flex-end;
    padding-right: 40px;
    font-family: "Oswald", "Arial Narrow", sans-serif;
    font-weight: 600; font-size: 36px; letter-spacing: .3px;
  }
  .contact-band__label { color: var(--paper); margin-right: 12px; }
  .contact-band__phone { color: var(--orange); }
</style>
</head>
<body>
  <section class="card card--front" aria-label="Card front">
    <div class="front__texture" role="img" aria-label="Faint repeated brand pattern in dark grey"></div>
    <div class="front__brand">
      <span class="front__dot"></span>
      <span class="front__name">HALLORAN FIELD SERVICES</span>
    </div>
    <p class="front__tagline">CUSTOMISED SPREADING</p>
  </section>

  <section class="card card--back" aria-label="Card back">
    <div class="back__brand">
      <span class="back__dot"></span>
      <span class="back__name">HALLORAN FIELD SERVICES</span>
    </div>
    <div class="back__divider"></div>
    <ul class="services">
      <li>Bulk fertilizer including Lime<br>Gypsum, Manure &amp; Compost</li>
      <li>Granular fertilizer including Single<br>Super, Urea, Terragran<br>Custom Blends</li>
      <li>Modern equipment</li>
      <li>Autosteer &amp; Variable Rate Capable</li>
      <li>Friendly &amp; Reliable Service</li>
    </ul>
    <div class="contact-band">
      <span class="contact-band__label">CONTACT GUS:</span>
      <span class="contact-band__phone">0417 552 308</span>
    </div>
  </section>
</body>
</html>
```